Classic and neutral book cover design

We are looking for a classic and neutral book cover design to be used as the template for a series of books to be published. We are hence looking for a template that will allow us to easily change the title name for all books in this series.
The use of very few colours (black and white is welcome) and few design elements is a big bonus. As a source of inspiration we would like to ask you to view the very simple and
If you think you have a cool idea that can add a twist to the formal classic look don't hesitate. Go for it !
Work will be done for a 30 year old Sweden based cultural non-profit called VĂ©ru (www.verufoundation.example). We work with the publishing and supporting of post-modern art and literature addressing contemporary topics but are also involved in assisting projects of cultural preservation.
Target Market(s)
The audience is expected to have some form of interest in culture but could range from hobbyist readers to tenure track scholars
Industry/Entity Type
Non-Profit
Requirements
Must have
- General:
- Classic and neutral feel
- Preferably very simple and few shapes
- usage of few colours (black and white is welcome)
Information to be displayed on the cover is:
- Author
- Title
- type of work e.g. play/novel (optional)
- publishing house (in this case "Veru Publishing")
Nice to have
- ideas to prevent it from become boring are of course welcome
Should not have
- - too many colours

```html
<!DOCTYPE html>
<html lang="lv">
<head>
<meta charset="utf-8">
<title>Vēstnesis – book cover</title>
<link rel="stylesheet" href="https://fonts.googleapis.com/css2?family=Jost:wght@600;700;800&display=swap">
<style>
  :root {
    --page-bg: #efede8;
    --cover-green: #9fa584;
    --ink: #23251f;
    --ornament-tone: #5d6350;
  }
  * { box-sizing: border-box; margin: 0; padding: 0; }
  html, body {
    width: 1200px;
    height: 1000px;
    overflow: hidden;
    background: var(--page-bg);
  }
  .cover {
    position: absolute;
    left: 260px;
    top: 67px;
    width: 682px;
    height: 861px;
    background: var(--cover-green);
    box-shadow: 0 2px 4px rgba(0, 0, 0, 0.18);
    font-family: "Jost", "Futura", sans-serif;
    color: var(--ink);
  }
  .ring-band {
    position: absolute;
    left: 6px;
    top: 6px;
    right: 12px;
    bottom: 8px;
    border: 14px solid var(--ornament-tone);
    border-radius: 7px;
  }
  .frame-line {
    position: absolute;
    border: 2.5px solid var(--ink);
  }
  .frame-outer  { left: 35px; top: 33px; right: 39px; bottom: 37px; }
  .frame-middle { left: 44px; top: 41px; right: 49px; bottom: 45px; }
  .frame-inner  { left: 53px; top: 50px; right: 59px; bottom: 55px; }
  .author,
  .title-block,
  .publisher {
    position: absolute;
    left: 0;
    width: 690px;
    text-align: center;
  }
  .author {
    top: 75px;
    font-size: 23px;
    font-weight: 700;
    letter-spacing: 0.3px;
  }
  .title-block { top: 365px; }
  .title {
    font-size: 43px;
    font-weight: 800;
    line-height: 1;
    letter-spacing: 0;
  }
  .work-type {
    margin-top: -1px;
    font-size: 16px;
    font-weight: 700;
    line-height: 1;
  }
  .publisher {
    top: 751px;
    font-size: 19px;
    font-weight: 700;
  }
</style>
</head>
<body>
  <main class="cover">
    <div class="ring-band" role="img" aria-label="Decorative border of linked rings"></div>
    <div class="frame-line frame-outer"></div>
    <div class="frame-line frame-middle"></div>
    <div class="frame-line frame-inner"></div>

    <p class="author">Aleksis Vētrainis</p>
    <div class="title-block">
      <h1 class="title">VĒSTNESIS</h1>
      <p class="work-type">luga</p>
    </div>
    <p class="publisher">Veru Publishing</p>
  </main>
</body>
</html>
```